holloway paving service

Needs to have phone number 0418259730 and email markholloway@brightmail.com.au.
ABN 62318470915
name mark holloway

For all your concreting solutions
Excavation
Exposed & colour concrete
House & shed slabs
Driveways
Landing & steps

Contact Information for Business Card

ph 0418259730
email markholloway@brightmail.com.au.
ABN 62318470915
name mark holloway

```html
<!DOCTYPE html>
<html lang="en">
<head>
<meta charset="utf-8">
<title>Holloway Paving Service – Business Card</title>
<link href="https://fonts.googleapis.com/css2?family=Lato:wght@400;700&family=Montserrat:wght@500;600&display=swap" rel="stylesheet">
<style>
  :root {
    --stage: #2b2b2d;
    --card: #1f2022;
    --card-back: #1c1d1f;
    --orange: #f26a21;
    --grey: #8a8b8d;
    --light: #c9cacc;
    --rule: #3e3f42;
    --blush: #f3d9cc;
  }
  * { box-sizing: border-box; margin: 0; padding: 0; }
  html, body { width: 1200px; height: 1108px; overflow: hidden; }
  body {
    background: var(--stage);
    font-family: "Lato", sans-serif;
    position: relative;
  }
  .card {
    position: absolute;
    top: 184px;
    width: 440px;
    height: 740px;
    border-radius: 22px;
    overflow: hidden;
  }
  .card--front { left: 120px; background: var(--card); }
  .card--back { left: 640px; background: var(--card-back); }

  /* Front */
  .brand {
    position: absolute;
    top: 110px;
    left: 0; right: 0;
    display: flex;
    align-items: center;
    justify-content: center;
    gap: 16px;
  }
  .brand__square {
    width: 46px; height: 46px;
    background: var(--orange);
  }
  .brand__name {
    font-family: "Montserrat", sans-serif;
    font-weight: 600;
    font-size: 22px;
    line-height: 1.2;
    letter-spacing: 0.5px;
    color: var(--orange);
    text-transform: uppercase;
  }
  .contact {
    position: absolute;
    top: 330px;
    left: 60px; right: 60px;
    text-align: center;
  }
  .contact__name {
    font-family: "Montserrat", sans-serif;
    font-weight: 600;
    font-size: 27px;
    letter-spacing: 0.5px;
  }
  .contact__first { color: var(--orange); }
  .contact__last { color: var(--grey); }
  .contact__line {
    color: var(--light);
    font-size: 19px;
    line-height: 1.45;
  }
  .rule {
    height: 1px;
    background: var(--rule);
    margin: 18px 30px;
  }
  .tagline {
    color: var(--orange);
    font-family: "Montserrat", sans-serif;
    font-weight: 500;
    font-size: 17px;
    text-transform: uppercase;
    margin-bottom: 10px;
  }
  .services { color: var(--grey); font-size: 19px; line-height: 1.35; }

  /* Back */
  .pattern-area {
    position: absolute;
    inset: 0;
    background: linear-gradient(160deg, #2a2b2e 0%, #1c1d1f 70%);
  }
  .back-brand {
    position: absolute;
    left: 0; right: 0;
    bottom: 110px;
    text-align: center;
    font-family: "Montserrat", sans-serif;
    font-weight: 600;
    font-size: 26px;
    line-height: 1.25;
    letter-spacing: 0.5px;
    color: var(--blush);
    text-transform: uppercase;
  }
</style>
</head>
<body>
  <section class="card card--front" aria-label="Business card front">
    <div class="brand">
      <div class="brand__square"></div>
      <div class="brand__name">Holloway Paving<br>Service</div>
    </div>
    <div class="contact">
      <h1 class="contact__name"><span class="contact__first">MARK</span> <span class="contact__last">HOLLOWAY</span></h1>
      <p class="contact__line">ABN 62318470915</p>
      <div class="rule"></div>
      <p class="contact__line">0418259730</p>
      <p class="contact__line">markholloway@brightmail.com.au</p>
      <div class="rule"></div>
      <p class="tagline">For all your concreting solutions</p>
      <p class="services">Excavation &nbsp;| &nbsp;Exposed &amp; colour concrete<br>House &amp; shed slabs &nbsp;| Driveways<br>Landing &amp; steps</p>
    </div>
  </section>

  <section class="card card--back" aria-label="Business card back">
    <div class="pattern-area" role="img" aria-label="Subtle dark repeating diamond pattern"></div>
    <div class="back-brand">Holloway Paving<br>Service</div>
  </section>
</body>
</html>
```